Web and Logo Design for eCommerce site

We're launching a sister brand and require a full design for the site.

The site must have an established feel and appeal to corporate and institutional buyers.
Updates

Just a note about the wireframe design:

The Search & Rescue / Coast Guard / NVDK, etc. in the header area aren't buttons or menu items, but rather just info (along the lines of a tagline).  Sort of a "who we serve" sort of thing.

Worth noting is that it's specifically geared towards LARGE BUYERS.  For example, a police force buying 200 headlamps and 85 pairs of gloves.  So they'll register + sign in and then add a bunch of items to a RFQ.

Aim for a professional, masculine design.

Target Market(s)

We will be selling outdoor gear to the military, law enforcement, fire and rescue and first responders.

Requirements
Must have
• We require:
- Logo (vector based)

Site:
- template page
* main site template, re-skinned version of our current site
* horizontal drop-down menu
- product listings page
* thumbnail view of products
- product details page
* including elements such as product image, color/size selector, descriptions and specs (again, based loosely on our current website)
- account management page
* illustrating basic data entry styles for text box, buttons, grid, etc.

The site needs to be given a responsive design, so 2 versions of each design should be presented for desktop + mobile views.

Additional funds are available if the designer is able to fully implement the designs into a responsive framework such as bootstrap.

Nice to have
• Clean, professional design similar to:

http://military.trailvexagear.com/gov/accessories/gloves.html

http://leaf.ombrivo.com/ProductFind.aspx?language=EN&category=Hardshell&subcat=Waterproof_Jackets

```html
<!DOCTYPE html>
<html lang="en">
<head>
<meta charset="utf-8">
<title>Vantor — Outdoor Gear for First Responders</title>
<link href="https://fonts.googleapis.com/css2?family=Arimo:wght@400;700&display=swap" rel="stylesheet">
<style>
  :root{
    --brand:#1e3f6a;
    --nav:#0d3a6b;
    --nav-text:#dfe6f0;
    --page:#ececec;
    --header:#f4f4f6;
    --text:#666;
    --muted:#8a8a8a;
    --rule:#d6d6d6;
    --footer:#0e325f;
    --footer-deep:#0a284c;
    --footer-text:#9fb2c8;
    --accent:#1f4690;
  }
  *{box-sizing:border-box;margin:0;padding:0}
  html,body{width:1200px;height:1004px;overflow:hidden}
  body{position:relative;background:var(--page);font-family:"Arimo",Arial,sans-serif;color:var(--text)}
  .abs{position:absolute}
  .top-strip{left:0;top:0;width:1200px;height:7px;background:var(--nav)}
  .site-header{left:0;top:7px;width:1200px;height:89px;background:var(--header)}
  .brand-name{left:167px;top:20px;font-size:44px;color:var(--brand);letter-spacing:.5px}
  .account-links{right:156px;top:17px;font-size:12px;color:var(--accent)}
  .who-we-serve{right:156px;top:51px;font-size:14.5px;color:#777;white-space:nowrap}
  .who-we-serve .lead{color:var(--accent)}
  .who-we-serve .sep{margin:0 10px;color:#999}
  .main-nav{left:0;top:96px;width:1200px;height:40px;background:var(--nav);border-bottom:3px solid #b9c0c8}
  .main-nav ul{list-style:none;display:flex;position:absolute;left:181px;top:11px;font-size:14.5px;color:var(--nav-text);white-space:nowrap}
  .main-nav li+li::before{content:"|";margin:0 19px 0 20px;color:#9fb2c8}
  .hero{left:0;top:139px;width:1200px;height:224px;background:linear-gradient(100deg,#3a3f47 0%,#7e838b 35%,#54595f 55%,#2f3338 100%)}
  .hero-arrow{top:241px}
  .hero-title{right:155px;top:188px;text-align:right;font-size:35px;line-height:42px;color:#cfd3d8}
  .categories{left:172px;top:381px;width:190px}
  .section-title{font-size:12.5px;color:var(--brand);letter-spacing:.3px}
  .categories ul{list-style:none;margin-top:10px;border-top:1px solid var(--rule)}
  .categories li{height:27.3px;line-height:27px;border-bottom:1px solid #dcdcdc;font-family:Verdana,"Arimo",sans-serif;font-size:11.5px;color:#777;padding-left:21px;position:relative}
  .categories li::before{content:"";position:absolute;left:7px;top:10px;border-left:7px solid #999;border-top:4px solid transparent;border-bottom:4px solid transparent}
  .cat-foot{left:172px;top:640px;width:193px;height:5px;background:#d4d4d4}
  .stamp{left:172px;top:654px;width:193px;height:146px;background:radial-gradient(ellipse at center,#f3e6e6 0%,#e7cccc 70%,#ececec 100%)}
  .stamp-foot{left:172px;top:801px;width:193px;height:4px;background:#dcdcdc}
  .welcome{left:410px;top:382px;font-size:12.5px;color:#555;letter-spacing:.3px}
  .welcome span{color:var(--brand)}
  .testimonial{left:862px;top:411px;width:175px;font-family:Verdana,"Arimo",sans-serif;font-size:11px;line-height:13px;color:#888}
  .rule-line{left:862px;top:506px;width:158px;height:1px;background:#ddd}
  .product-image{background:linear-gradient(135deg,#fbfbfb,#eeeeee);border:6px solid #e4e4e4}
  .product-info{font-family:Verdana,"Arimo",sans-serif;font-size:11.3px;line-height:13px;color:#777}
  .product-info h3{font-family:"Arimo",Arial,sans-serif;font-weight:400;font-size:12.5px;color:var(--brand);padding-bottom:9px;border-bottom:1px solid #e0e0e0;margin-bottom:12px;width:115px}
  .more{font-family:Verdana,"Arimo",sans-serif;font-size:11.3px;color:#777;letter-spacing:.5px}
  .modal{left:361px;top:394px;width:497px;height:251px;background:#fff;border:2px solid #1d3f86;border-radius:4px}
  .modal-close{left:455px;top:12px}
  .modal-text{position:absolute;left:25px;top:53px;width:455px;font-size:14.3px;line-height:17px;color:#333}
  .signup{position:absolute;left:66px;top:162px;display:flex;height:40px}
  .signup-input{width:246px;height:40px;background:linear-gradient(#e9e9e9,#f2f2f2);border:1px solid #c8c8c8;border-right:0;border-radius:4px 0 0 4px;font-size:14.5px;color:#999;text-align:center;line-height:38px}
  .signup-button{width:98px;height:40px;background:var(--accent);border:1px solid #173a7a;border-radius:0 4px 4px 0;color:#fff;font-size:14.5px;text-align:center;line-height:38px}
  .site-footer{left:158px;top:835px;width:886px;height:169px;background:var(--footer)}
  .footer-base{left:158px;top:969px;width:886px;height:35px;background:var(--footer-deep)}
  .footer-col{top:17px}
  .footer-col h4{font-weight:400;font-size:12.5px;color:#c8d3e0;letter-spacing:.3px;padding-bottom:10px;border-bottom:1px solid #274a75}
  .footer-menu{list-style:none;margin-top:6px}
  .footer-menu li{font-family:Verdana,"Arimo",sans-serif;font-size:11.3px;color:var(--footer-text);height:22.7px;line-height:22px;padding-left:21px;position:relative}
  .footer-menu li::before{content:"";position:absolute;left:9px;top:7px;border-left:7px solid #8ea3bb;border-top:4px solid transparent;border-bottom:4px solid transparent}
  .footer-copy{font-family:Verdana,"Arimo",sans-serif;font-size:11.3px;line-height:13px;color:#7f95ae}
  .pay-chip{width:30px;height:20px;border-radius:2px;background:#c9d2dc}
  .social-chip{width:20px;height:20px;background:#3a5a80}
  .copyright{left:158px;top:984px;width:886px;text-align:center;font-family:Verdana,"Arimo",sans-serif;font-size:10.3px;color:#8ea3bb;letter-spacing:.4px}
</style>
</head>
<body>
  <div class="abs top-strip"></div>

  <header class="abs site-header">
    <div class="abs brand-name">Vantor</div>
    <div class="abs account-links">Login &nbsp;|&nbsp; Register</div>
    <div class="abs who-we-serve"><span class="lead">Search &amp; Rescue</span><span class="sep">|</span>Coast Guard<span class="sep">|</span>NVDK<span class="sep">|</span>Fire<span class="sep">|</span>Military<span class="sep">|</span>Law Enforcement</div>
  </header>

  <nav class="abs main-nav">
    <ul>
      <li>Rescue Gear</li><li>Footwear</li><li>Clothing</li><li>Tents, Mats, Sleeping Bags</li><li>Camping Gear</li><li>Snow Sports</li><li>Brands</li>
    </ul>
  </nav>

  <section class="abs hero" role="img" aria-label="Ice climber in a red jacket and helmet ascending a frozen waterfall"></section>
  <svg class="abs hero-arrow" style="left:21px" width="32" height="32" viewBox="0 0 32 32"><circle cx="16" cy="16" r="14" fill="none" stroke="#e5e5e5" stroke-width="2"/><path d="M19 8 L10 16 L19 24 Z" fill="#e5e5e5"/></svg>
  <svg class="abs hero-arrow" style="left:1135px" width="32" height="32" viewBox="0 0 32 32"><circle cx="16" cy="16" r="14" fill="none" stroke="#e5e5e5" stroke-width="2"/><path d="M13 8 L22 16 L13 24 Z" fill="#e5e5e5"/></svg>
  <h1 class="abs hero-title" style="font-weight:400">Great Outdoor<br>Gear for Canada<br>First Responders</h1>

  <aside class="abs categories">
    <h2 class="section-title" style="font-weight:400">OUR CATEGORIES</h2>
    <ul>
      <li>Rescue Gear</li><li>Footwear</li><li>Clothing</li><li>Tents &amp; Mats</li><li>Sleeping Bags</li><li>Camping Gear</li><li>Snow Sports</li><li>Brands</li>
    </ul>
  </aside>
  <div class="abs cat-foot"></div>
  <div class="abs stamp" role="img" aria-label="Red rubber stamp reading 100% ship free"></div>
  <div class="abs stamp-foot"></div>

  <h2 class="abs welcome" style="font-weight:400">WELCOME TO <span>VANTOR OUTDOOR PRO SUPPLY</span></h2>
  <p class="abs testimonial">... Overall the customer service that assisted me with sizing,</p>
  <div class="abs rule-line"></div>

  <div class="abs product-image" style="left:419px;top:523px;width:162px;height:123px" role="img" aria-label="Product photo"></div>
  <div class="abs product-image" style="left:732px;top:523px;width:162px;height:123px" role="img" aria-label="Ridgeline skis product photo"></div>
  <div class="abs product-info" style="left:907px;top:524px">
    <h3>RIDGELINE SKIS</h3>
    <p>$ 749.00<br>Summit Line Skis</p>
  </div>
  <div class="abs more" style="left:980px;top:621px">MORE...</div>

  <div class="abs product-image" style="left:419px;top:681px;width:162px;height:123px" role="img" aria-label="Orange climbing skins product photo"></div>
  <div class="abs product-info" style="left:589px;top:683px">
    <h3>GRANITE PEAK</h3>
    <p>$ 139.95<br>Traverse Nylon STS<br>125mm Skins</p>
  </div>
  <div class="abs more" style="left:662px;top:782px">MORE...</div>

  <div class="abs product-image" style="left:732px;top:681px;width:162px;height:123px" role="img" aria-label="Green ski binding product photo"></div>
  <div class="abs product-info" style="left:907px;top:683px">
    <h3>ALPKOR</h3>
    <p>$ 990.00<br>Bastion 16 Limited<br>Edition Binding</p>
  </div>
  <div class="abs more" style="left:980px;top:782px">MORE...</div>

  <div class="abs modal" role="dialog" aria-label="Register">
    <svg class="abs modal-close" width="28" height="28" viewBox="0 0 28 28"><circle cx="14" cy="14" r="13.5" fill="#1f3f8a"/><path d="M9.5 9.5 L18.5 18.5 M18.5 9.5 L9.5 18.5" stroke="#fff" stroke-width="3" stroke-linecap="round"/></svg>
    <p class="modal-text">Please register to Enter and Enjoy Canada’s best selection of outdoor gear at special pricing and terms that reflect your, commitment to service and duty, your unique position and credential</p>
    <div class="signup">
      <div class="signup-input">Enter Your Email ID</div>
      <div class="signup-button">Register</div>
    </div>
  </div>

  <footer class="abs site-footer">
    <div class="abs footer-col" style="left:13px;top:20px;width:210px">
      <h4>MAIN MENU</h4>
      <ul class="footer-menu"><li>Home</li><li>About Us</li><li>Products</li><li>Contact Us</li></ul>
    </div>
    <div class="abs footer-col" style="left:235px;top:20px;width:220px">
      <h4>LATEST NEWS</h4>
      <p class="footer-copy" style="margin-top:11px">Printer and scanner complement each other. This apparently con-fusing statement might annoy you for a moment;</p>
    </div>
    <div class="abs footer-col" style="left:454px;top:17px;width:213px">
      <h4>PAYMENT METHODS</h4>
      <p class="footer-copy" style="margin-top:13px;padding-left:8px">In our shop the following payment methods are accepted:</p>
      <div style="display:flex;gap:5px;margin:17px 0 0 8px">
        <div class="pay-chip"></div><div class="pay-chip"></div><div class="pay-chip"></div><div class="pay-chip"></div>
      </div>
    </div>
    <div class="abs footer-col" style="left:673px;top:17px;width:205px">
      <h4>CONTACT US</h4>
      <div class="footer-copy" style="position:absolute;left:20px;top:37px;white-space:nowrap">
        <svg width="14" height="11" viewBox="0 0 14 11" style="vertical-align:-1px;margin-right:6px"><path d="M1 4 Q7 -1 13 4 L11 5 L10 3 L4 3 L3 5 Z M3 6 L11 6 L12 11 L2 11 Z" fill="#9fb2c8"/></svg>+ 1234 5678 91
      </div>
      <div class="footer-copy" style="position:absolute;left:20px;top:66px;white-space:nowrap">
        <svg width="16" height="11" viewBox="0 0 16 11" style="vertical-align:-1px;margin-right:10px"><rect x="0.5" y="0.5" width="15" height="10" fill="none" stroke="#9fb2c8"/><path d="M0.5 0.5 L8 6 L15.5 0.5" fill="none" stroke="#9fb2c8"/></svg>info@vantorgear.com
      </div>
      <div style="position:absolute;left:52px;top:91px;display:flex;gap:3px">
        <div class="social-chip"></div><div class="social-chip"></div><div class="social-chip"></div><div class="social-chip"></div>
      </div>
    </div>
  </footer>
  <div class="abs footer-base"></div>
  <div class="abs copyright">© 2014 VANTOR. ALL RIGHTS RESERVED.</div>
</body>
</html>
```